Brochure required

Looking at getting business brochure designed for my solar sales company. i will require a range of products to be listed on the brochure I require a simple/ elegent / professional looking brochure.

I am happy to provide designer with all the required information that must go into the brochure. otherwise please visit www.quillebartow.com.au and view the products which i would like to allocate into the brochure aswell as our company logo and a little about me section

```html
<!DOCTYPE html>
<html lang="en">
<head>
<meta charset="utf-8">
<title>Quillebartow – Solar Brochure</title>
<link rel="stylesheet" href="https://fonts.googleapis.com/css2?family=Lato:wght@400;700;900&display=swap">
<style>
  :root{
    --bg:#ece4df;
    --paper:#ffffff;
    --green:#1db38b;
    --blue:#1f8dc4;
    --ink:#3a3a3a;
    --muted:#7a7a7a;
    --gold:#c9a227;
    --sky:#8fb7dc;
    --grass:#5f8f3a;
  }
  *{box-sizing:border-box;margin:0;padding:0}
  html,body{width:768px;height:1200px;overflow:hidden}
  body{background:var(--bg);font-family:"Lato",sans-serif;color:var(--ink);position:relative}
  .spread{position:absolute;left:30px;width:708px;height:500px;display:flex;box-shadow:0 6px 18px rgba(0,0,0,.12)}
  .spread--outer{top:50px}
  .spread--inner{top:640px}
  .page{position:relative;width:354px;height:500px;background:var(--paper);overflow:hidden}
  .page + .page{border-left:1px solid #e6e6e6}
  .art{position:absolute;left:0;top:0}
  .brand{display:flex;align-items:center;gap:6px;font-weight:900;font-size:19px;color:var(--ink);letter-spacing:.2px}
  .brand__dot{width:14px;height:14px;background:var(--green);display:block}
  .brand--small{font-size:12px;gap:4px}
  .brand--small .brand__dot{width:9px;height:9px}

  /* front cover */
  .cover__brand{position:absolute;top:44px;left:0;right:0;justify-content:center}
  .cover__title{position:absolute;top:80px;left:0;right:0;text-align:center;line-height:1.02}
  .cover__title .l1{display:block;color:var(--blue);font-size:25px;font-weight:700}
  .cover__title .l2{display:block;color:var(--ink);font-size:25px;font-weight:700}

  /* back cover */
  .contact{position:absolute;top:318px;left:0;right:0;text-align:center;z-index:1}
  .contact .brand{justify-content:center}
  .contact__cta{margin-top:6px;color:var(--blue);font-size:11px;font-weight:700;letter-spacing:.5px}
  .contact__phone{font-size:22px;font-weight:700;color:var(--ink);margin-top:1px}
  .contact__icon{display:block;margin:10px auto 3px}
  .contact__line{font-size:9px;color:var(--muted)}

  /* inside */
  .intro{position:absolute;top:24px;left:26px;right:26px;font-size:7px;line-height:1.45;color:var(--muted)}
  .product{position:absolute;left:22px;right:22px}
  .product--one{top:82px}
  .product--two{top:190px}
  .product__panel{position:absolute;left:18px;top:0;width:88px;height:62px;background:linear-gradient(135deg,#1d3f8a,#3f6fc9);border:2px solid #d8dde8}
  .product--two .product__panel{background:linear-gradient(135deg,#0f1420,#2a3142)}
  .product__badge{position:absolute;left:0;top:36px;width:48px;height:20px;background:#fff;border:2px solid var(--green);border-radius:4px}
  .product__name{position:absolute;left:116px;top:4px;color:var(--blue);font-size:11px;font-weight:700}
  .product__lead{position:absolute;left:116px;top:20px;right:0;font-size:7px;line-height:1.45;color:var(--muted)}
  .product__body{position:absolute;left:0;top:70px;right:0;font-size:7px;line-height:1.45;color:var(--muted)}

  .section{position:absolute;left:24px;right:24px}
  .section--care{top:24px}
  .section--audit{top:190px}
  .section__title{color:var(--blue);font-size:11px;font-weight:700;margin-bottom:5px}
  .section p{font-size:7px;line-height:1.45;color:var(--muted);margin-bottom:5px}
  .section__text{width:170px}
  .section__photo{position:absolute;right:0;width:120px;height:80px;background:linear-gradient(160deg,#bcd3ea,#3f6fb0)}
  .section--care .section__photo{top:80px}
  .section--audit .section__photo{top:100px;background:linear-gradient(160deg,#c8d6e6,#2c4f86)}
  .ticks{list-style:none}
  .ticks li{display:flex;align-items:center;gap:5px;font-size:7px;color:var(--muted);margin-bottom:3px}
  .ticks li::before{content:"";width:7px;height:7px;border-radius:50%;border:1.5px solid var(--gold);flex:none}
  .band{position:absolute;left:0;top:0}
</style>
</head>
<body>

<!-- Outer spread: back cover + front cover -->
<section class="spread spread--outer">
  <article class="page back-cover">
    <svg class="art" width="354" height="500" viewBox="0 0 354 500">
      <defs>
        <linearGradient id="installer" x1="0" y1="0" x2="1" y2="1">
          <stop offset="0" stop-color="#6f9fd4"/>
          <stop offset=".55" stop-color="#c9d8ea"/>
          <stop offset="1" stop-color="#27324a"/>
        </linearGradient>
        <linearGradient id="wave" x1="0" y1="0" x2="1" y2="0">
          <stop offset="0" stop-color="#5fc2c9"/>
          <stop offset="1" stop-color="#1f6fb8"/>
        </linearGradient>
      </defs>
      <path d="M160,0 A170,170 0 0 1 190,300" fill="none" stroke="var(--gold)" stroke-width="7"/>
      <circle cx="40" cy="140" r="152" fill="url(#installer)" role="img" aria-label="Photo of an installer in a helmet fitting a solar panel on a roof"/>
      <path d="M0,475 C110,490 250,485 354,440 L354,500 L0,500 Z" fill="url(#wave)"/>
    </svg>
    <div class="contact">
      <div class="brand brand--small"><span class="brand__dot"></span>quillebartow</div>
      <div class="contact__cta">CALL US NOW</div>
      <div class="contact__phone">0400 555 218</div>
      <svg class="contact__icon" width="11" height="11" viewBox="0 0 12 12"><circle cx="6" cy="6" r="6" fill="var(--blue)"/><rect x="3" y="4" width="6" height="4" fill="none" stroke="#fff" stroke-width=".8"/><path d="M3,4 L6,6.3 L9,4" fill="none" stroke="#fff" stroke-width=".8"/></svg>
      <div class="contact__line">hello@quillebartow.com.au</div>
      <svg class="contact__icon" width="11" height="11" viewBox="0 0 12 12"><circle cx="6" cy="6" r="6" fill="var(--blue)"/><circle cx="6" cy="6" r="3" fill="none" stroke="#fff" stroke-width=".8"/><path d="M3,6 H9 M6,3 V9" stroke="#fff" stroke-width=".6"/></svg>
      <div class="contact__line">www.quillebartow.com.au</div>
    </div>
  </article>

  <article class="page front-cover">
    <svg class="art" width="354" height="500" viewBox="0 0 354 500">
      <defs>
        <linearGradient id="field" x1="0" y1="0" x2="0" y2="1">
          <stop offset="0" stop-color="#9cc1e4"/>
          <stop offset=".35" stop-color="#f4e9c9"/>
          <stop offset=".6" stop-color="#33415c"/>
          <stop offset="1" stop-color="var(--grass)"/>
        </linearGradient>
      </defs>
      <path d="M125,205 C100,300 95,420 150,500 L354,500 L354,245 C300,218 200,205 125,205 Z" fill="var(--green)"/>
      <circle cx="275" cy="395" r="148" fill="url(#field)" stroke="#fff" stroke-width="6" role="img" aria-label="Photo of a solar panel array in a grassy field under a bright sun"/>
    </svg>
    <div class="brand cover__brand"><span class="brand__dot"></span>quillebartow</div>
    <h1 class="cover__title"><span class="l1">Energy solutions for a</span><span class="l2">changing world</span></h1>
  </article>
</section>

<!-- Inner spread -->
<section class="spread spread--inner">
  <svg class="band" width="708" height="500" viewBox="0 0 708 500" style="z-index:2;pointer-events:none">
    <defs>
      <linearGradient id="farm" x1="0" y1="0" x2="0" y2="1">
        <stop offset="0" stop-color="#a9c8e6"/>
        <stop offset=".5" stop-color="#3c5a86"/>
        <stop offset="1" stop-color="#6f9a48"/>
      </linearGradient>
    </defs>
    <path d="M0,500 L0,395 Q250,340 420,430 Q520,480 708,470 L708,500 Z" fill="url(#farm)" role="img" aria-label="Wide photo of a large solar farm in open country"/>
    <path d="M0,395 Q250,340 420,430 Q520,480 708,470" fill="none" stroke="var(--green)" stroke-width="5"/>
  </svg>

  <article class="page inside-left">
    <p class="intro">We partner with trusted panel makers to bring you reliable, efficient solar products chosen for Australian homes and businesses, backed by strong warranties and careful installation.</p>
    <div class="product product--one">
      <div class="product__panel" role="img" aria-label="Product photo of a blue polycrystalline solar panel"></div>
      <div class="product__badge"></div>
      <h2 class="product__name">SOLARA 270W</h2>
      <p class="product__lead">World class, tested for harsh weather and built for long, steady output.</p>
      <p class="product__body">This panel sets a high mark for value and suits most rooftop systems across the country.</p>
    </div>
    <div class="product product--two">
      <div class="product__panel" role="img" aria-label="Product photo of a black monocrystalline solar panel"></div>
      <div class="product__badge"></div>
      <h2 class="product__name">SOLARA ARC PERC 60M 300W</h2>
      <p class="product__lead">A highly efficient mono panel from a top tier maker at a fair price.</p>
      <p class="product__body">Its cell design lifts output while keeping a clean look on any roof.</p>
    </div>
  </article>

  <article class="page inside-right">
    <div class="section section--care">
      <h2 class="section__title">SYSTEM MAINTENANCE &amp; CLEANING</h2>
      <div class="section__text">
        <p>Like any machine, your solar system needs regular care to run safely and well.</p>
        <p>Dust, leaves and bird mess build up over time and cut output. Regular cleaning keeps your panels working at full strength.</p>
      </div>
      <div class="section__photo" role="img" aria-label="Photo of panels being cleaned with a brush"></div>
    </div>
    <div class="section section--audit">
      <h2 class="section__title">SOLAR INSTALLATION AUDITING</h2>
      <div class="section__text">
        <p>We check that your system meets current standards and is safe, tidy and correctly installed.</p>
        <p>Our team gives you a clear report and simple next steps.</p>
        <ul class="ticks">
          <li>Certificate history check</li>
          <li>Wiring and safety compliance</li>
          <li>Output and shading review</li>
        </ul>
      </div>
      <div class="section__photo" role="img" aria-label="Photo of a technician inspecting a rooftop panel"></div>
    </div>
  </article>
</section>

</body>
</html>
```